Website design for company that sells taximeters and has a taxi dispatch call center, webstore neede

Need a website with a shop with at least 20 articles, in two languages, possibly by using a purchased theme (not purchased yet).The company provides equipments and dispatch solutions for taxi companies. Typical yellow and black theme

Target Market(s)

Taxi companies

Industry/Entity Type

Taxi

Number of Pages Required

3 page

Font styles to use
Sans Serif

Colors
fbed22
000000

Requirements
Must have
• - webstore for at least 20 articles
• - Documents folder where to put pdf material related to taximeters
• - contact form message submission
Nice to have
• Feedback section
Should not have
• Blogs,

```html
<!DOCTYPE html>
<html lang="en">
<head>
<meta charset="utf-8">
<title>Cabmetra – Services</title>
<link rel="stylesheet" href="https://fonts.googleapis.com/css2?family=Hind:wght@400;500;600;700&family=Open+Sans:wght@400;600;700;800&display=swap">
<style>
:root{
  --yellow:#f0c640;
  --yellow-bright:#fbd12a;
  --ink:#333333;
  --dark:#1d1d1d;
  --black:#0b0b0b;
  --white:#ffffff;
  --mist:#f3f3f3;
}
*{margin:0;padding:0;box-sizing:border-box}
html,body{width:850px;height:1200px;overflow:hidden;background:var(--white)}
body{position:relative;font-family:"Hind",sans-serif;color:var(--ink)}
.abs{position:absolute}

/* hero */
.hero{left:0;top:0;width:850px;height:203px;
  background:linear-gradient(180deg,#3a3431 0%,#2a2624 45%,#4a403a 70%,#1e1c1c 100%)}
.hero-shade{left:0;top:0;width:850px;height:203px;
  background:radial-gradient(ellipse at 50% 60%,rgba(120,100,90,.35),transparent 60%)}
.brand{left:106px;top:10px;font-family:"Open Sans",sans-serif;font-weight:800;font-size:17px;letter-spacing:1px;color:var(--yellow-bright)}
.nav{left:271px;top:15px;display:flex;gap:7px;font-family:"Open Sans",sans-serif;font-weight:700;font-size:7px;letter-spacing:.6px;color:var(--white)}
.nav .current{color:var(--yellow-bright)}
.phone{left:535px;top:10px;display:flex;align-items:center;gap:8px;font-family:"Open Sans",sans-serif;font-weight:700;font-size:8px;letter-spacing:1.4px;color:var(--yellow-bright)}
.lang{left:630px;top:14px;font-family:"Open Sans",sans-serif;font-weight:700;font-size:7px;color:var(--white);letter-spacing:.5px}
.search{left:696px;top:10px;width:108px;height:20px;border:1.5px solid var(--yellow-bright);border-radius:10px;
  font-family:"Open Sans",sans-serif;font-size:9px;color:#cfcfcf;letter-spacing:1px;padding:3px 0 0 11px}
.search svg{position:absolute;right:8px;top:4px}
.hero-title{left:0;width:874px;top:82px;text-align:center;font-family:"Open Sans",sans-serif;font-weight:700;font-size:20px;letter-spacing:3px;color:var(--white)}
.hero-sub{left:0;width:874px;top:114px;text-align:center;font-family:"Open Sans",sans-serif;font-weight:700;font-size:7.5px;letter-spacing:1.4px;color:var(--white)}

/* intro */
.intro-panel{left:425px;top:203px;width:425px;height:284px;background:var(--yellow)}
.intro-notch{left:402px;top:312px}
.headline{font-weight:600;font-size:24px;line-height:25px;letter-spacing:-.8px;color:var(--ink)}
.headline::after{content:"";display:block;width:56px;height:3px;background:var(--yellow);margin:7px 0 0 3px}
.intro-head{left:56px;top:308px}
.offer-title{left:425px;width:415px;top:253px;text-align:center;font-weight:600;font-size:21px;color:var(--ink)}
.offer-list{top:296px;list-style:none;font-size:9.6px;font-weight:500;letter-spacing:-.2px;color:var(--ink)}
.offer-list li{height:16.2px;padding-left:13px;position:relative}
.offer-list li::before{content:"";position:absolute;left:0;top:3px;width:5px;height:5px;border-radius:50%;background:var(--ink)}
.col-a{left:487px}.col-b{left:655px}

/* infrastructure */
.infra-panel{left:0;top:487px;width:425px;height:280px;background:var(--dark)}
.infra-notch{left:425px;top:604px}
.infra-copy{left:37px;top:587px;width:360px;font-size:9.2px;font-weight:500;line-height:16.2px;letter-spacing:-.25px;color:var(--yellow-bright)}
.infra-head{left:501px;top:598px}

/* stats */
.stats{left:0;top:767px;width:850px;height:169px;
  background:radial-gradient(ellipse at 15% 45%,#4a3b35 0%,transparent 32%),radial-gradient(ellipse at 55% 20%,#2a3040 0%,transparent 30%),linear-gradient(90deg,#1a1716,#15151a 60%,#121212)}
.stats-title{left:0;width:862px;top:812px;text-align:center;font-weight:600;font-size:17px;letter-spacing:-.8px;color:var(--white)}
.stat{top:848px;width:120px;text-align:center;color:var(--yellow-bright)}
.stat b{display:block;font-weight:600;font-size:27px;letter-spacing:-1px;line-height:30px}
.stat span{display:block;font-size:11px;font-weight:500;line-height:10.5px;letter-spacing:-.4px}
.divider{top:858px;width:1.5px;height:30px;background:var(--white)}

/* call to action */
.cta{left:0;top:940px;width:850px;height:92px;background:var(--mist)}
.cta-text{left:0;width:898px;top:971px;text-align:center;font-family:"Open Sans",sans-serif;font-weight:600;font-size:18.5px;letter-spacing:.5px;color:var(--black)}

/* footer */
.footer{left:0;top:1032px;width:850px;height:168px;background:var(--black)}
.foot-col{top:1061px;width:125px;font-family:"Open Sans",sans-serif;font-size:6px;line-height:10.3px;color:var(--white)}
.foot-col h4{font-weight:700;font-size:6.2px;margin-bottom:7px;letter-spacing:.2px}
.foot-col .hl{color:var(--yellow-bright)}
.socials{display:flex;gap:5px;margin-top:1px}
.socials i{display:block;width:8px;height:8px;border-radius:50%;background:var(--white)}
.foot-rule{left:179px;top:1133px;width:500px;height:1px;background:#888}
.legal{left:179px;top:1140px;font-family:"Open Sans",sans-serif;font-size:5.3px;color:var(--white)}
.legal .hl{color:var(--yellow-bright)}
</style>
</head>
<body>

<header>
  <div class="abs hero" role="img" aria-label="Photo of taxis driving across a steel truss bridge at dusk"></div>
  <div class="abs hero-shade"></div>
  <div class="abs brand">CABMETRA</div>
  <nav class="abs nav">
    <span class="current">HOME</span><span>SHOP</span><span>SERVICES</span><span>INSTALLERS</span><span>CONTACT US</span><span>JOIN US</span>
  </nav>
  <div class="abs phone">
    <svg width="14" height="14" viewBox="0 0 24 24" fill="none" stroke="#ffffff" stroke-width="1.6"><path d="M5 3h4l2 5-2.5 1.5a11 11 0 0 0 6 6L16 13l5 2v4a2 2 0 0 1-2 2A16 16 0 0 1 3 5a2 2 0 0 1 2-2z"/><path d="M15 3a6 6 0 0 1 6 6M15 7a2 2 0 0 1 2 2"/></svg>
    555.210.4478
  </div>
  <div class="abs lang">ENG ˅</div>
  <div class="abs search">search
    <svg width="11" height="11" viewBox="0 0 24 24" fill="none" stroke="#ffffff" stroke-width="2"><circle cx="10" cy="10" r="7"/><path d="M15 15l6 6"/></svg>
  </div>
  <h1 class="abs hero-title">SERVICES</h1>
  <p class="abs hero-sub">FIND OUT HOW WE CAN MAKE YOUR FLEET MORE SUCCESSFUL</p>
</header>

<section>
  <div class="abs intro-panel"></div>
  <svg class="abs intro-notch" width="24" height="46" viewBox="0 0 24 46"><path d="M24 0L0 23L24 46Z" fill="#f0c640"/></svg>
  <h2 class="abs headline intro-head">More than just selling goods,<br>we offer services as well.</h2>
  <h3 class="abs offer-title">Offerings</h3>
  <ul class="abs offer-list col-a">
    <li>No nec meis docendi</li><li>Cum electram definitionem</li><li>Rebum munere ex mea</li><li>Lorem ipsum dolor sit amet</li><li>Vide convenire abhorreant</li><li>Consul ullamcorper cu ius</li><li>No nec meis docendi</li>
  </ul>
  <ul class="abs offer-list col-b">
    <li>No nec meis docendi</li><li>Cum electram definitionem</li><li>Rebum munere ex mea</li><li>Lorem ipsum dolor sit amet</li><li>Vide convenire abhorreant</li><li>Consul ullamcorper cu ius</li><li>No nec meis docendi</li>
  </ul>
</section>

<section>
  <div class="abs infra-panel"></div>
  <svg class="abs infra-notch" width="24" height="34" viewBox="0 0 24 34"><path d="M0 0L24 17L0 34Z" fill="#1d1d1d"/></svg>
  <p class="abs infra-copy">Lorem ipsum dolor sit amet, consectetuer adipiscing elit. Aenean commodo ligula eget dolor. Aenean massa. Cum sociis natoque penatibus et magnis dis parturient montes, nascetur ridiculus mus. Donec qu Lorem ipsum dolor sit amet, consectetuer adipiscing elit. Aenean commodo ligula eget dolor. Aenean massa. Cum sociis natoque penatibus et magnis dis parturient montes, nascetur ridiculus mus. Donec quLorem ipsum dolor sit amet, consectetuer adipiscing elit. Aenean commodo ligula eget dolor.</p>
  <h2 class="abs headline infra-head">We thrive on having a secure<br>infrastructure in place.</h2>
</section>

<section>
  <div class="abs stats" role="img" aria-label="Dark blurred photo of a taxi interior at night"></div>
  <h2 class="abs stats-title">BECAUSE NUMBERS COUNT</h2>
  <div class="abs stat" style="left:215px"><b>100%</b><span>Dispatch<br>infrastructure</span></div>
  <div class="abs divider" style="left:328px"></div>
  <div class="abs stat" style="left:332px"><b>66%</b><span>Productivity<br>improvement</span></div>
  <div class="abs divider" style="left:449px"></div>
  <div class="abs stat" style="left:438px"><b>45%</b><span>Growth and<br>demand</span></div>
  <div class="abs divider" style="left:549px"></div>
  <div class="abs stat" style="left:548px"><b>90%</b><span>Customer Success<br>improvement</span></div>
</section>

<section>
  <div class="abs cta"></div>
  <h2 class="abs cta-text">ASK ABOUT HOW OUR SERVICES CAN HELP YOU</h2>
</section>

<footer>
  <div class="abs footer"></div>
  <div class="abs foot-col" style="left:179px">
    <h4>ABOUT <span class="hl">CABMETRA</span></h4>
    We provide quality dispatch and meter equipment for independent taxi &amp; fleet vendors.
  </div>
  <div class="abs foot-col" style="left:307px">
    <h4>CONTACT INFO</h4>
    Shop Office: (555) 410-2286<br>Customer service: (555) 7731-0592<br>Email: <span class="hl">hello@cabmetra.com</span>
  </div>
  <div class="abs foot-col" style="left:435px">
    <h4>HOURS OF SERVICE</h4>
    Monday - Friday: 09:00AM - 09:00PM<br>Saturday: 09:00AM - 07:00PM<br>Sunday: Closed
  </div>
  <div class="abs foot-col" style="left:562px">
    <h4>LINK <span class="hl">US</span></h4>
    <div class="socials"><i></i><i></i><i></i><i></i><i></i></div>
  </div>
  <div class="abs foot-rule"></div>
  <p class="abs legal">© 2018 <span class="hl">Cabmetra.com</span> &nbsp;&nbsp;&nbsp;&nbsp;&nbsp;&nbsp;| &nbsp;Trademarks and brands are the property of their respective owners.</p>
</footer>

</body>
</html>
```